RTavenor Business Cards & Letterhead

I have a logo but need a design for some new business cards. We are a Design-Build Firm that specializes in the design and construction of commercial projects.
the cards need to be professional. no cartoon stuff.
i would like to have the cards in AI format so I can update the card as needed. Logo is provided.
Our Address is: 4187 Marlowe Ct. Apex, North Carolina 27614

```html
<!DOCTYPE html>
<html lang="en">
<head>
<meta charset="utf-8">
<title>RTavenor Letterhead &amp; Business Cards</title>
<link href="https://fonts.googleapis.com/css2?family=Open+Sans:wght@400;600;700&family=Lato:wght@400;700&family=Tangerine:wght@700&display=swap" rel="stylesheet">
<style>
  :root {
    --brand-blue: #0a6aa8;
    --brand-gray: #6f6f71;
    --ink: #222;
    --paper: #ffffff;
    --backdrop: #e9e6e1;
  }
  * { box-sizing: border-box; margin: 0; padding: 0; }
  html, body { width: 1200px; height: 942px; overflow: hidden; }
  body { background: var(--backdrop); position: relative; font-family: "Open Sans", sans-serif; color: var(--ink); }

  .brand-mark { display: flex; align-items: center; gap: 0.18em; color: var(--brand-gray); font-family: "Open Sans", sans-serif; font-weight: 700; letter-spacing: -0.01em; line-height: 1; }
  .brand-mark .brand-square { width: 0.62em; height: 0.62em; background: var(--brand-blue); flex: none; }

  /* Letterhead */
  .letterhead { position: absolute; left: 84px; top: 89px; width: 541px; height: 764px; background: var(--paper); box-shadow: 0 2px 6px rgba(0,0,0,.18); overflow: hidden; }
  .letterhead .brand-mark { position: absolute; left: 27px; top: 53px; font-size: 31px; }
  .letterhead-contact { position: absolute; left: 388px; top: 37px; border-left: 1.5px solid var(--brand-blue); padding-left: 9px; font-size: 10.4px; line-height: 12px; color: #222; }
  .letterhead-contact .address { margin-bottom: 6px; }
  .contact-line { display: flex; align-items: center; gap: 4px; }
  .contact-line svg { width: 7px; height: 7px; fill: var(--brand-blue); flex: none; }

  .letter { position: absolute; left: 27px; top: 175px; width: 488px; font-family: "Lato", sans-serif; font-size: 11.2px; line-height: 12px; color: #1d1d1d; }
  .letter p { margin-bottom: 12px; text-align: justify; }
  .letter .date, .letter .recipient { text-align: left; }
  .letter .date { margin-bottom: 14px; }
  .letter .recipient { margin-bottom: 14px; }
  .letter .salutation { font-weight: 700; font-size: 13.5px; margin: 2px 0 16px; }
  .letter .closing { margin-top: 20px; }
  .letter .signature { font-family: "Tangerine", cursive; font-size: 30px; font-weight: 700; margin-top: 50px; line-height: 1; }

  .footer-band { position: absolute; left: 0; bottom: 0; display: block; }

  /* Business cards */
  .card { position: absolute; left: 673px; width: 444px; height: 254px; background: var(--paper); border-radius: 22px; box-shadow: 0 2px 6px rgba(0,0,0,.2); overflow: hidden; }
  .card-front { top: 201px; display: flex; align-items: center; justify-content: center; }
  .card-front .brand-mark { font-size: 58px; margin-top: -18px; }
  .card-back { top: 488px; }
  .card-back .brand-mark { position: absolute; left: 34px; top: 115px; font-size: 29px; }
  .card-details { position: absolute; left: 259px; top: 55px; height: 143px; border-left: 1.5px solid var(--brand-blue); padding-left: 11px; font-size: 12.6px; line-height: 16px; color: #2a2a2a; }
  .card-details .name { font-size: 18.5px; font-weight: 700; color: var(--brand-blue); line-height: 20px; letter-spacing: 0.01em; }
  .card-details .title { margin-bottom: 12px; }
  .card-details .contact-line svg { width: 9px; height: 9px; }
  .card-details .address { margin-top: 13px; }
</style>
</head>
<body>

<section class="letterhead">
  <div class="brand-mark"><span class="brand-square"></span>RTavenor</div>

  <address class="letterhead-contact" style="font-style:normal">
    <div class="address">4187 Marlowe Ct. Apex,<br>North Carolina 27614</div>
    <div class="contact-line"><svg viewBox="0 0 10 10"><path d="M2 0.5l2 2-1 1.2c.6 1.3 1.6 2.3 2.9 2.9l1.2-1 2 2-1.3 1.9C4 9 .6 5.8.3 1.7z"/></svg>123 456 789</div>
    <div class="contact-line"><svg viewBox="0 0 10 10"><path d="M0 2h10v6H0z M0 2l5 3.5L10 2" stroke="#fff" stroke-width=".8"/></svg>info@rtavenor-mail.com</div>
    <div class="contact-line"><svg viewBox="0 0 10 10"><circle cx="5" cy="5" r="5"/></svg>www.yourwebsite.com</div>
  </address>

  <article class="letter">
    <p class="date">January-03-2020</p>
    <p class="recipient">Mr, Alan Pierce<br>President</p>
    <p class="recipient">Northgate Corporation<br>123 Street Name, Suite# 10<br>City, State, 120023</p>
    <p class="salutation">Dear Mr, Alan</p>
    <p>Lorem ipsum dolor sit amet, consectetur adipiscing elit, sed do eiusmod tempor incididunt ut labore et dolore magna aliqua. Ut enim ad minim veniam, quis nostrud exercitation ullamco laboris nisi ut aliquip ex ea commodo consequat. Duis aute irure dolor in reprehenderit in voluptate velit esse cillum dolore eu fugiat nulla pariatur.</p>
    <p>Lorem ipsum dolor sit amet, consectetur adipiscing elit, sed do eiusmod tempor incididunt ut labore et dolore magna aliqua. Ut enim ad minim veniam, quis nostrud exercitation ullamco laboris nisi ut aliquip ex ea commodo consequat. Duis aute irure dolor in reprehenderit in voluptate velit esse cillum dolore eu fugiat nulla pariatur.</p>
    <p>Lorem ipsum dolor sit amet, consectetur adipiscing elit, sed do eiusmod tempor incididunt ut labore et dolore magna aliqua. Ut enim ad minim veniam, quis nostrud exercitation ullamco laboris nisi ut aliquip ex ea commodo consequat.</p>
    <p>Excepteur sint occaecat cupidatat non proident, sunt in culpa qui officia deserunt mollit anim id est laborum. re et dolore magnam aliquam quaerat voluptatem.</p>
    <p class="closing">Regards</p>
    <p class="signature">Laura Bennett</p>
  </article>

  <svg class="footer-band" width="541" height="36" viewBox="0 0 541 36" aria-hidden="true">
    <polygon points="0,5 341,5 335,11 0,11" fill="var(--brand-gray)"/>
    <polygon points="352,0 541,0 541,36 0,36 0,16 338,16" fill="var(--brand-blue)"/>
  </svg>
</section>

<section class="card card-front">
  <div class="brand-mark"><span class="brand-square"></span>RTavenor</div>
</section>

<section class="card card-back">
  <div class="brand-mark"><span class="brand-square"></span>RTavenor</div>
  <div class="card-details">
    <div class="name">DANIEL REYES</div>
    <div class="title">Managing Director</div>
    <div class="contact-line"><svg viewBox="0 0 10 10"><path d="M2 0.5l2 2-1 1.2c.6 1.3 1.6 2.3 2.9 2.9l1.2-1 2 2-1.3 1.9C4 9 .6 5.8.3 1.7z"/></svg>123 456 789</div>
    <div class="contact-line"><svg viewBox="0 0 10 10"><path d="M0 2h10v6H0z M0 2l5 3.5L10 2" stroke="#fff" stroke-width=".8"/></svg>info@rtavenor-mail.com</div>
    <div class="contact-line"><svg viewBox="0 0 10 10"><circle cx="5" cy="5" r="5"/></svg>www.yourwebsite.com</div>
    <div class="address">4187 Marlowe Ct. Apex,<br>North Carolina 27614</div>
  </div>
  <svg class="footer-band" width="444" height="24" viewBox="0 0 444 24" aria-hidden="true">
    <polygon points="0,4 275,4 270,10 0,10" fill="var(--brand-gray)"/>
    <polygon points="284,0 444,0 444,24 0,24 0,13 272,13" fill="var(--brand-blue)"/>
  </svg>
</section>

</body>
</html>
```